Current state of Man's Soul Christian view

I would like an improvement of my design or a reimagining of my design to help people visualize what happens to the soul after we die. The second picture "screenshot 2023" is not my design but gives another idea.

For further information, there are 4 "time" frames that could be sectioned off. Eden is one time. Then adam rebellion and pre messiah earth (with hades/ Sheol). The third time frame is Jesus death, resurrection with the current state of earth. The 4th time frame is the "heavenly realm" which is across all 3 times and is unchanged.

For color ideas, please see my website www.lanternfieldnotes.org which has my color theme. But the death of Jesus I would like in some type of red as well as the death of believers.

My goal is something simple, engaging, and easy to understand. If you have any questions please lmk.
Thank you for considering my project.

```html
<!DOCTYPE html>
<html lang="en">
<head>
<meta charset="utf-8">
<title>Current State of Man's Soul</title>
<link href="https://fonts.googleapis.com/css2?family=Bebas+Neue&family=Manrope:wght@600;700;800&display=swap" rel="stylesheet">
<style>
  :root{
    --night:#162a45;
    --night-deep:#070b12;
    --panel:#0a0d14;
    --gold:#f0a92b;
    --gold-line:#d9891f;
    --white:#ffffff;
    --ink:#1c2233;
    --navy-ink:#1b2f63;
    --sky-a:#dfe9ef;
    --sky-b:#7fb0cf;
    --red:#e41c23;
    --title:#e6f3fb;
    --torment-a:#f3551c;
    --torment-b:#6e1208;
    --paradise-a:#fbe08a;
    --paradise-b:#b07612;
    --rule:rgba(255,255,255,.55);
  }
  *{margin:0;padding:0;box-sizing:border-box}
  html,body{width:1200px;height:849px;overflow:hidden;background:var(--night-deep)}
  .poster{position:relative;width:1200px;height:849px;overflow:hidden;font-family:"Manrope",sans-serif;color:var(--white)}
  .scene{position:absolute;inset:0;background:
      radial-gradient(ellipse at 58% 30%,#35507a 0%,rgba(53,80,122,0) 45%),
      linear-gradient(180deg,#1a2f4f 0%,#1d3250 45%,#243a5c 62%,#0b111c 78%,#04070c 100%)}
  .figure{position:absolute;left:5px;top:0;width:80px;height:209px;
      background:linear-gradient(180deg,rgba(240,169,43,.25),rgba(224,138,30,.9));border-radius:0 0 40px 40px}
  .title{position:absolute;left:102px;top:33px;font-family:"Bebas Neue",sans-serif;font-size:64px;line-height:64px;
      letter-spacing:.5px;color:var(--title);text-shadow:2px 2px 0 #5d7f99}
  .rule-top{position:absolute;left:0;top:23px;width:825px;height:1.5px;background:var(--gold-line)}
  .rule-bottom{position:absolute;left:52px;top:99px;width:766px;height:1.5px;background:var(--gold-line)}
  .heaven{position:absolute;left:112px;top:140px;width:1056px;height:90px;border:1.5px solid var(--gold);border-radius:10px;
      background:linear-gradient(90deg,var(--sky-a) 0%,#c9dbe6 45%,var(--sky-b) 100%);}
  .heaven-label{position:absolute;left:0;right:0;top:14px;text-align:center;color:var(--ink);font-weight:700;font-size:33px;letter-spacing:-.3px}
  .panel{position:absolute;border:1px solid rgba(255,255,255,.18);border-radius:10px}
  .panel-left{left:86px;top:271px;width:477px;height:338px;background:linear-gradient(90deg,var(--panel) 0%,var(--panel) 78%,rgba(10,13,20,.35) 100%)}
  .panel-right{left:750px;top:271px;width:414px;height:338px;background:rgba(8,11,18,.55)}
  .death-bar{position:absolute;left:86px;top:589px;width:1078px;height:20px;background:var(--red);border-radius:0 0 8px 8px}
  .death-tab{position:absolute;left:119px;top:563px;width:98px;height:27px;background:var(--red);border-radius:4px 4px 0 0;
      font-weight:700;font-size:21px;line-height:28px;text-align:center}
  .eden{position:absolute;left:22px;top:447px;transform:rotate(-90deg);transform-origin:left top;font-weight:700;font-size:25px}
  .label{position:absolute;font-weight:700;line-height:1.08}
  .adam{left:102px;top:384px;font-size:22px}
  .hades-top{left:279px;top:307px;font-size:22px}
  .jesus-death{left:476px;top:349px;font-size:22px;text-align:center;width:76px}
  .believers{right:78px;top:281px;font-size:22px;text-align:right}
  .non-believers{right:78px;top:516px;font-size:22px;text-align:right}
  .gate{position:absolute;top:619px;font-weight:600;font-size:16px}
  .hades-bottom{position:absolute;left:893px;top:815px;font-size:15px;font-weight:600}
  .resurrection{position:absolute;left:576px;top:349px;width:131px;height:53px;background:var(--white);border:2px solid #24304a;border-radius:7px;
      color:var(--navy-ink);font-weight:700;font-size:17px;line-height:19px;text-align:center;padding-top:7px}
  .spirit{position:absolute;left:746px;top:258px;width:130px;height:87px;border-radius:8px;border:1px solid rgba(255,255,255,.3);
      background:radial-gradient(circle at 50% 48%,#ffffff 0%,#eef3f8 30%,#6f86a6 62%,#1c2f50 100%);
      color:var(--ink);font-weight:700;font-size:17px;line-height:18px;text-align:center;padding-top:10px}
  .globe{position:absolute;border-radius:50%;overflow:hidden;border:2px solid rgba(255,255,255,.85)}
  .split{display:flex}
  .split .half{flex:1;position:relative}
  .torment{background:radial-gradient(circle at 60% 70%,var(--torment-a),var(--torment-b))}
  .paradise{background:radial-gradient(circle at 40% 60%,var(--paradise-a),var(--paradise-b));border-left:3px solid var(--white)}
  .half span{position:absolute;font-weight:700;color:var(--white);text-shadow:0 1px 3px rgba(0,0,0,.6)}
  .paradise span{color:var(--ink);text-shadow:none}
  .hades-circle{left:233px;top:348px;width:224px;height:224px}
  .hades-circle .half span{top:36px;font-size:18px}
  .hades-circle .torment span{right:6px}
  .hades-circle .paradise span{left:8px}
  .hades-circle-now{left:854px;top:636px;width:176px;height:176px}
  .hades-circle-now .half span{top:29px;font-size:14px}
  .hades-circle-now .torment span{right:4px}
  .hades-circle-now .paradise span{left:4px}
  .earth{background:radial-gradient(circle at 40% 35%,#9fd0e8 0%,#3f7fbf 35%,#1f4f8c 70%,#13325e 100%)}
  .earth-now{left:826px;top:335px;width:224px;height:224px}
  .earth-old{left:260px;top:643px;width:170px;height:170px;background:radial-gradient(circle at 45% 40%,#3f7f86 0%,#2a4a4a 45%,#1a2326 80%,#d46a1a 100%)}
  .earth-band{position:absolute;left:0;right:0;bottom:0;background:rgba(226,230,234,.93);color:var(--ink);font-weight:700;text-align:center}
  .earth-now .earth-band{height:76px;font-size:21px;line-height:24px;padding-top:8px}
  .earth-old .earth-band{height:58px;font-size:16px;line-height:18px;padding-top:4px}
  svg.overlay{position:absolute;left:0;top:0}
</style>
</head>
<body>
<div class="poster">
  <div class="scene" role="img" aria-label="Night landscape with moonlit sky, silhouetted trees, mountains and a river"></div>
  <div class="figure" role="img" aria-label="Golden illustration of a falling human figure beneath rays of light"></div>

  <div class="rule-top"></div>
  <h1 class="title">CURRENT STATE OF MAN'S SOUL</h1>
  <div class="rule-bottom"></div>

  <div class="heaven" role="img" aria-label="Heavenly sky with clouds and radiant throne">
    <div class="heaven-label">3rd Heaven - God’s Heavenly Throne</div>
  </div>

  <div class="panel panel-left"></div>
  <div class="panel panel-right"></div>

  <svg class="overlay" width="1200" height="849" viewBox="0 0 1200 849" aria-hidden="true">
    <g stroke="var(--rule)" stroke-width="1.2" fill="none">
      <line x1="285" y1="554" x2="285" y2="660"/>
      <line x1="341" y1="554" x2="341" y2="645"/>
      <line x1="377" y1="554" x2="377" y2="645"/>
      <line x1="407" y1="554" x2="407" y2="660"/>
      <line x1="874" y1="540" x2="874" y2="655"/>
      <line x1="930" y1="555" x2="930" y2="640"/>
      <line x1="969" y1="555" x2="969" y2="640"/>
      <line x1="998" y1="540" x2="998" y2="655"/>
      <line x1="457" y1="460" x2="557" y2="460"/>
      <circle cx="562" cy="460" r="9" stroke="rgba(255,255,255,.8)"/>
    </g>
    <g stroke="var(--gold)" stroke-width="8" fill="none" stroke-linecap="round" stroke-linejoin="round">
      <path d="M562 460 H635 Q645 460 645 450 V268"/>
      <path d="M726 244 V451 Q726 461 736 461 H782"/>
      <path d="M1058 461 H1129 Q1139 461 1139 451 V276"/>
      <path d="M1058 480 H1124 Q1134 480 1134 490 V716 Q1134 726 1124 726 H1078"/>
    </g>
    <g fill="var(--gold)">
      <polygon points="645,240 629,278 661,278"/>
      <polygon points="804,461 774,447 774,475"/>
      <polygon points="1139,246 1125,275 1153,275"/>
      <polygon points="1050,726 1082,710 1082,742"/>
    </g>
    <g stroke="var(--gold)" stroke-width="4.5" fill="none" stroke-linecap="round" stroke-linejoin="round">
      <polyline points="64,406 71,413 64,420"/><polyline points="72,406 79,413 72,420"/>
      <polyline points="503,299 512,307 521,299"/><polyline points="503,308 512,316 521,308"/>
      <polyline points="496,425 487,434 496,443"/><polyline points="505,425 496,434 505,443"/>
      <polyline points="305,630 313,622 321,630"/><polyline points="305,638 313,630 321,638"/>
      <polyline points="384,630 392,622 400,630"/><polyline points="384,638 392,630 400,638"/>
      <polyline points="894,628 902,620 910,628"/><polyline points="894,636 902,628 910,636"/>
      <polyline points="974,628 982,620 990,628"/><polyline points="974,636 982,628 990,636"/>
    </g>
  </svg>

  <div class="death-bar"></div>
  <div class="death-tab">DEATH</div>

  <div class="eden">Eden</div>
  <div class="label adam">Adam<br>Rebellion</div>
  <div class="label hades-top">Hades/Sheol</div>
  <div class="label jesus-death">JESUS<br>DEATH</div>

  <div class="globe split hades-circle">
    <div class="half torment" role="img" aria-label="Fiery red illustration of the place of torment"><span>Torment</span></div>
    <div class="half paradise" role="img" aria-label="Golden illustration of a gate and stairway to paradise"><span>Paradise</span></div>
  </div>

  <div class="resurrection">Jesus<br>Resurrection</div>
  <div class="spirit">Holy<br>Spirit<br>Descends</div>

  <div class="globe earth earth-now" role="img" aria-label="Planet Earth seen from space">
    <div class="earth-band">Current<br>Fallen Earth</div>
  </div>

  <div class="label believers">Believers<br>in Jesus</div>
  <div class="label non-believers">Non<br>-Believers</div>

  <div class="gate" style="left:195px">Wide Gate</div>
  <div class="gate" style="left:416px">Narrow Gate</div>
  <div class="gate" style="left:783px">Wide Gate</div>
  <div class="gate" style="left:1010px">Narrow Gate</div>

  <div class="globe earth-old" role="img" aria-label="Darkened, burning illustration of the pre-messiah fallen Earth">
    <div class="earth-band">Pre-Messiah<br>Fallen Earth</div>
  </div>

  <div class="globe split hades-circle-now">
    <div class="half torment" role="img" aria-label="Fiery red illustration of the place of torment"><span>Torment</span></div>
    <div class="half paradise" role="img" aria-label="Golden illustration of a gate and stairway to paradise"><span>Paradise</span></div>
  </div>
  <div class="hades-bottom">Hades/Sheol</div>
</div>
</body>
</html>
```